Quillbrookes websites redesign

Www.quill-brookes.com needs to be redesigned along with updations. The incremental material will be provided for the updations. We are looking for complete redesign of the pages with the new content. The complete write up will be provided soon

Target Market(s)

Global

Coding

Coded - Design and coding required

Number of Pages Required

5+ page

Requirements
Must have
• A clean and slick design for the Consulting.
Should not have
• Too many pictures which reduces the speed of the site

```html
<!DOCTYPE html>
<html lang="en">
<head>
<meta charset="utf-8">
<title>Quillbrookes Consultancy Limited</title>
<link href="https://fonts.googleapis.com/css2?family=Open+Sans:wdth,wght@75..100,300..800&display=swap" rel="stylesheet">
<style>
:root{
  --blue:#41a8d4;
  --blue-deep:#3a9fca;
  --button:#3296bf;
  --maroon:#5a1d1f;
  --ink:#3c3c3c;
  --muted:#666;
  --white:#fff;
  --black:#000;
  --charcoal:#2b2b2b;
}
*{box-sizing:border-box;margin:0;padding:0}
html,body{width:1200px;height:2239px;overflow:hidden}
body{font-family:"Open Sans",Arial,sans-serif;color:var(--ink);background:var(--white);position:relative}
.abs{position:absolute}

.top-rule{left:0;top:0;width:1200px;height:5px;background:linear-gradient(90deg,var(--maroon) 50%,var(--blue) 50%)}
.site-header{left:0;top:5px;width:1200px;height:98px;background:var(--white)}
.brand{left:98px;top:32px;display:flex;align-items:center;gap:10px}
.brand-mark{width:36px;height:36px;border-radius:50%;background:var(--blue)}
.brand-name{font-size:32px;font-weight:400;color:var(--maroon);letter-spacing:-.3px}
.main-nav{top:44px;left:0;width:1200px;font-size:14px;color:var(--maroon)}
.main-nav span{position:absolute}
.main-nav .active{color:var(--blue)}
.search{left:1085px;top:45px}

.hero{left:0;top:103px;width:1200px;height:479px;background:
  radial-gradient(ellipse at 30% 30%,rgba(200,215,240,.55),transparent 45%),
  radial-gradient(ellipse at 75% 20%,rgba(230,200,190,.6),transparent 35%),
  linear-gradient(180deg,#4a5f94 0%,#2f4a82 45%,#1c3568 100%)}
.hero-title{right:96px;top:356px;font-size:33px;font-weight:700;font-stretch:75%;color:var(--white);text-shadow:0 1px 3px rgba(0,0,0,.5)}
.hero-text{right:96px;top:412px;width:560px;text-align:right;font-size:14px;line-height:25.5px;font-stretch:80%;color:var(--white);text-shadow:0 1px 2px rgba(0,0,0,.6)}
.hero-arrow{top:340px}

.about-photo{left:107px;top:648px;width:465px;height:339px;background:linear-gradient(160deg,#d6d6d6,#8a8a8a 55%,#4a4a4a);box-shadow:0 0 0 1px #ccc}
h2.section-title{font-size:36px;font-weight:400;color:var(--maroon);line-height:1}
.body-copy{font-size:12.4px;line-height:22.4px;text-align:justify;color:var(--ink)}
.btn{display:flex;align-items:center;justify-content:center;background:var(--button);color:var(--white);font-size:13.5px;border-radius:2px;box-shadow:0 2px 0 #2a7ea2}

.cases{left:0;top:1054px;width:1200px;height:446px;background:linear-gradient(180deg,#4aacd6,#3fa5d1)}
.cases-title{left:0;top:1084px;width:1200px;text-align:center;font-size:36px;color:var(--white);font-weight:400}
.cases-sub{left:0;top:1140px;width:1200px;text-align:center;font-size:15px;line-height:22px;color:var(--white)}
.case{width:260px;text-align:center;color:var(--white)}
.case-ring{position:absolute;width:126px;height:126px;border:1.5px solid rgba(255,255,255,.9);border-radius:50%;display:flex;align-items:center;justify-content:center}
.case-name{font-size:15px;font-weight:600;line-height:23px}
.case-text{font-size:12.5px;line-height:22.5px}

.founder-photo{left:619px;top:1564px;width:466px;height:342px;background:linear-gradient(180deg,#3b3f8a 0%,#51457c 55%,#7a4650 80%,#3a2f4a 100%);box-shadow:0 0 0 4px #f1f1f1}

.newsletter{left:0;top:1970px;width:1200px;height:102px;background:var(--blue-deep)}
.news-title{left:243px;top:1992px;font-size:17px;color:var(--white)}
.news-sub{left:243px;top:2024px;font-size:13px;color:var(--white)}
.news-input{left:625px;top:2000px;width:324px;height:42px;background:var(--white);font-size:12px;color:#555;padding:13px 15px}
.news-btn{left:949px;top:2000px;width:127px;height:42px;background:var(--charcoal);color:var(--white);font-size:15px;display:flex;align-items:center;justify-content:center}

.site-footer{left:0;top:2072px;width:1200px;height:167px;background:var(--black)}
.social{left:0;top:2099px;width:1200px;display:flex;justify-content:center;gap:5px}
.social span{width:34px;height:34px;border:1.5px solid var(--white);border-radius:50%}
.foot-nav{left:0;top:2152px;width:1200px;display:flex;justify-content:center;gap:22px;font-size:11px;color:var(--white)}
.copyright{left:0;top:2182px;width:1200px;text-align:center;font-size:11px;color:var(--white)}
</style>
</head>
<body>
<div class="abs top-rule"></div>
<header class="abs site-header"></header>
<div class="abs brand"><span class="brand-mark"></span><span class="brand-name">Quillbrookes</span></div>
<nav class="abs main-nav">
  <span class="active" style="left:444px">Home</span>
  <span style="left:526px">Founder</span>
  <span style="left:625px">Consultancy</span>
  <span style="left:749px">System</span>
  <span style="left:841px">Case studies</span>
  <span style="left:967px">Contact</span>
</nav>
<svg class="abs search" width="18" height="18" viewBox="0 0 18 18"><circle cx="7.5" cy="7.5" r="5.2" fill="none" stroke="#41a8d4" stroke-width="2.4"/><line x1="11.4" y1="11.4" x2="16" y2="16" stroke="#41a8d4" stroke-width="2.8" stroke-linecap="round"/></svg>

<section class="abs hero" role="img" aria-label="Hand typing on a keyboard with a glowing world map overlay"></section>
<svg class="abs hero-arrow" style="left:42px" width="14" height="44" viewBox="0 0 14 44"><polyline points="12,2 2,22 12,42" fill="none" stroke="#fff" stroke-width="1.5"/></svg>
<svg class="abs hero-arrow" style="left:1140px" width="14" height="44" viewBox="0 0 14 44"><polyline points="2,2 12,22 2,42" fill="none" stroke="#fff" stroke-width="1.5"/></svg>
<h1 class="abs hero-title">QUILLBROOKES CONSULTANCY LIMITED</h1>
<p class="abs hero-text">The consultancy for the Banks and Non Banking Financial Institutions is focused on risk mitigation techniques, Export Credit Agency business and trade origination and distribution strategies along with raising long term liabilities.</p>

<div class="abs about-photo" role="img" aria-label="Business team smiling around a table reviewing papers"></div>
<h2 class="abs section-title" style="left:615px;top:662px">About Us</h2>
<p class="abs body-copy" style="left:615px;top:708px;width:478px">Quillbrookes Consultancy Limited capitalizes on synergies arising from trade and investment linkages between countries and knowledge of traditional and non-traditional pools of liquidity to provide consultancy services to Emerging country banks, Corporates and SMEs.<br>The Consultancy provides bank neutral views to Corporates and SMEs in Asian emerging markets and helps in improving financial structure and efficient use of funds. Our endeavor is to provide a distinct bottom line advantage to our clients. The primary focus is in regionalisation of the banking relationship across the globe, providing structured finance solutions and off balance sheet solutions.</p>
<a class="abs btn" style="left:616px;top:928px;width:95px;height:42px">Read More</a>

<section class="abs cases"></section>
<h2 class="abs cases-title">Case Studies</h2>
<p class="abs cases-sub">Some of the deals completed by QCL are summarised below to describe the range of activities<br>undertaken with Corporates</p>

<div class="case-ring" style="left:143px;top:1204px">
  <svg width="50" height="50" viewBox="0 0 50 50" fill="none" stroke="#fff" stroke-width="2.6"><path d="M17 8h16l9 9v25H17v-8"/><path d="M33 8v9h9"/><path d="M17 21v-4M8 27h20M22 21l6 6-6 6"/></svg>
</div>
<div class="case-ring" style="left:409px;top:1204px">
  <svg width="56" height="50" viewBox="0 0 56 50" fill="#fff"><polygon points="28,4 52,16 4,16"/><rect x="6" y="18" width="44" height="3"/><rect x="10" y="23" width="5" height="16"/><rect x="19" y="23" width="5" height="16"/><rect x="28" y="23" width="5" height="16"/><rect x="37" y="23" width="5" height="16"/><rect x="4" y="41" width="48" height="5"/></svg>
</div>
<div class="case-ring" style="left:674px;top:1204px">
  <svg width="52" height="52" viewBox="0 0 52 52" fill="none" stroke="#fff" stroke-width="2.4"><rect x="22" y="6" width="22" height="12" transform="rotate(-20 33 12)"/><rect x="24" y="14" width="22" height="12" transform="rotate(-10 35 20)"/><path d="M8 32l10-8h12l-4 8H18M14 46l6-8h14l10-10"/></svg>
</div>
<div class="case-ring" style="left:941px;top:1204px">
  <svg width="44" height="56" viewBox="0 0 44 56" fill="none" stroke="#fff" stroke-width="2.6"><path d="M22 4a16 16 0 0 0-10 28c3 3 4 6 4 9h12c0-3 1-6 4-9A16 16 0 0 0 22 4z"/><path d="M16 46h12M17 51h10"/><rect x="14" y="12" width="16" height="10" fill="#fff" stroke="none"/></svg>
</div>

<div class="abs case" style="left:76px;top:1346px"><p class="case-name">Export Credit Agency backed<br>long term Project financing</p><p class="case-text" style="margin-top:8px">The consultancy for the Banks and<br>Non Banking Financial Institutions<br>is focused on risk mitigation...</p></div>
<div class="abs case" style="left:342px;top:1358px"><p class="case-name">Regional/Local banks</p><p class="case-text" style="margin-top:19px">The consultancy for the Banks and<br>Non Banking Financial Institutions<br>is focused on risk mitigation...</p></div>
<div class="abs case" style="left:607px;top:1364px"><p class="case-name">Structured Financing</p><p class="case-text" style="margin-top:13px">The consultancy for the Banks and<br>Non Banking Financial Institutions<br>is focused on risk mitigation...</p></div>
<div class="abs case" style="left:874px;top:1364px"><p class="case-name">Bank Lines Business</p><p class="case-text" style="margin-top:13px">The consultancy for the Banks and<br>Non Banking Financial Institutions<br>is focused on risk mitigation...</p></div>

<h2 class="abs section-title" style="left:114px;top:1580px">Founder</h2>
<p class="abs body-copy" style="left:116px;top:1626px;width:478px">Quillbrookes Consultancy Limited capitalizes on synergies arising from trade and investment linkages between countries and knowledge of traditional and non-traditional pools of liquidity to provide consultancy services to Emerging country banks, Corporates and SMEs.<br>The Consultancy provides bank neutral views to Corporates and SMEs in Asian emerging markets and helps in improving financial structure and efficient use of funds. Our endeavor is to provide a distinct bottom line advantage to our clients. The primary focus is in regionalisation of the banking relationship across the globe, providing structured finance solutions and off balance sheet solutions.</p>
<a class="abs btn" style="left:116px;top:1846px;width:96px;height:40px">Read More</a>
<div class="abs founder-photo" role="img" aria-label="Founder speaking at a podium with flowers in front of a conference banner"></div>

<section class="abs newsletter"></section>
<svg class="abs" style="left:122px;top:1988px" width="96" height="72" viewBox="0 0 96 72" fill="none" stroke="rgba(255,255,255,.18)" stroke-width="3"><rect x="10" y="14" width="70" height="48" transform="rotate(-15 45 38)"/><polyline points="10,20 48,46 80,6" transform="rotate(-5 45 38)"/></svg>
<p class="abs news-title">JOIN OUR NEWSLETTER</p>
<p class="abs news-sub">Lorem ipsum dolor sit amet, consectetur</p>
<div class="abs news-input">Enter your E - mail</div>
<div class="abs news-btn">SUBSCRIBE</div>

<footer class="abs site-footer"></footer>
<div class="abs social" aria-label="Social links"><span></span><span></span><span></span><span></span><span></span></div>
<nav class="abs foot-nav"><span>HOME</span><span>FOUNDER</span><span>CONSULTANCY</span><span>SYSTEM</span><span>CASE STUDIES</span><span>CONTACT</span></nav>
<p class="abs copyright">Copyright @ 2016. © Quillbrookes Consultancy Limited&nbsp; All Rights Reserved.</p>
</body>
</html>
```